Business Card Re-Design/Update

We'd like to update out business cards. I've included our current "Style guide" which has the colour scheme of the organisation in it. I've also included the branding files with logos etc in them.

I've also included a copy of one of our existing cards so that you can see how ugly/dated they look. I'd like a fresh modern corporate look.

Target Market(s)

These are for our clients, potential clients, industry contacts - like all business cards

Contact Information for Business Card

Name
Position
Company Address - Level 1, 47 Fernby Street, Carlow Qld 4072
Direct Phone
mobile
Email
Website -www.korvalit.com.au
Logo

Colors

Designer to choose colors to be used in the design.

Requirements
Must have
• Main Logo
• Cards will need to be editable to be able to personalize them for each new employee.
Nice to have
• The MapOut, ShipWell, KeepSteady would be okay to have if they can be sensibly and professionally added to the look without detracting from the main imagery.
• Maybe they could go on the back of the card? will leave this to your creative discretion as to whether/where they fit.
Should not have
• Should not have decorative or script fonts

```html
<!DOCTYPE html>
<html lang="en">
<head>
<meta charset="utf-8">
<title>korvalIT business card</title>
<link rel="stylesheet" href="https://fonts.googleapis.com/css2?family=Arimo:wght@400;700&display=swap">
<style>
  :root {
    --stage: #2a2a2a;
    --card: #f6f6f6;
    --brand-red: #d42a2f;
    --ink: #3a3a3a;
    --ink-soft: #555555;
    --white: #ffffff;
  }
  * { box-sizing: border-box; margin: 0; padding: 0; }
  html, body {
    width: 1200px;
    height: 997px;
    overflow: hidden;
    background: var(--stage);
    font-family: "Arimo", Arial, sans-serif;
  }
  .stage {
    position: relative;
    width: 1200px;
    height: 997px;
  }
  .card {
    position: absolute;
    top: 340px;
    width: 520px;
    height: 318px;
    background: var(--card);
    border-radius: 18px;
    overflow: hidden;
  }
  .card--back { left: 60px; }
  .card--front { left: 620px; }

  /* back */
  .back-wordmark {
    position: absolute;
    top: 62px;
    left: 0;
    width: 100%;
    text-align: center;
    font-size: 50px;
    font-weight: 400;
    color: var(--ink-soft);
    letter-spacing: 1px;
  }
  .back-wordmark .mark-square {
    display: block;
    width: 34px;
    height: 34px;
    margin: 0 auto 10px;
    background: var(--brand-red);
  }
  .service-band {
    position: absolute;
    left: 0;
    top: 168px;
    width: 100%;
    height: 104px;
    background: var(--brand-red);
    display: flex;
    justify-content: space-around;
    align-items: center;
  }
  .service {
    text-align: center;
    color: var(--white);
    font-size: 20px;
    font-weight: 400;
  }
  .service .service-square {
    display: block;
    width: 16px;
    height: 16px;
    margin: 0 auto 8px;
    border: 2px solid var(--white);
  }

  /* front */
  .front-logo {
    position: absolute;
    top: 34px;
    left: 34px;
    display: flex;
    align-items: center;
    gap: 12px;
    font-size: 34px;
    font-weight: 400;
    color: var(--ink);
  }
  .front-logo .mark-square {
    width: 28px;
    height: 28px;
    background: var(--brand-red);
  }
  .person {
    position: absolute;
    top: 128px;
    left: 34px;
  }
  .person-name {
    font-size: 16px;
    font-weight: 700;
    color: var(--brand-red);
    letter-spacing: 0.5px;
  }
  .person-role {
    font-size: 13px;
    color: var(--ink);
    margin-top: 2px;
  }
  .address {
    position: absolute;
    top: 196px;
    left: 34px;
    font-size: 13px;
    line-height: 18px;
    color: var(--brand-red);
  }
  .contact-list {
    position: absolute;
    top: 238px;
    left: 34px;
    list-style: none;
    font-size: 14px;
    line-height: 21px;
    color: var(--ink);
  }
  .contact-list li {
    display: flex;
    align-items: center;
    gap: 8px;
  }
  .contact-list .bullet {
    width: 9px;
    height: 9px;
    border-radius: 50%;
    background: var(--brand-red);
  }
  .website {
    position: absolute;
    right: 30px;
    top: 196px;
    font-size: 15px;
    font-weight: 700;
    color: var(--brand-red);
    letter-spacing: 0.3px;
  }
</style>
</head>
<body>
<main class="stage">
  <section class="card card--back" aria-label="Business card back">
    <div class="back-wordmark"><span class="mark-square"></span>korvalIT</div>
    <div class="service-band">
      <div class="service"><span class="service-square"></span>MapOut</div>
      <div class="service"><span class="service-square"></span>ShipWell</div>
      <div class="service"><span class="service-square"></span>KeepSteady</div>
    </div>
  </section>

  <section class="card card--front" aria-label="Business card front">
    <div class="front-logo"><span class="mark-square"></span>korvalIT</div>
    <div class="person">
      <p class="person-name">MARTA VELLING</p>
      <p class="person-role">Director</p>
    </div>
    <p class="address">Level 1, 47 Fernby Street,<br>Carlow Qld 4072</p>
    <ul class="contact-list">
      <li><span class="bullet"></span>1300 555 019</li>
      <li><span class="bullet"></span>+61 7 3900 0142</li>
      <li><span class="bullet"></span>hello@korvalit.com.au</li>
    </ul>
    <p class="website">www.korvalit.com.au</p>
  </section>
</main>
</body>
</html>
```